Black Granite Web Design Project

We are looking for a design for a new company that will be selling Black Granite slabs and tiles. We will be selling to both end-consumers and granite installers. We have already settled on a logo and hopefully this will give an idea of what we like in our designs. We are not going to be selling online but want people to call us so the site is basically an enhanced business card. We will be focusing a lot on SEO so the design will have to keep that in mind.

We would like to keep the design in 1024x768 to make it easily view-able on all devices.

Regarding navigation there should only be a few sub-pages, like "Granite Slabs", "Granite Tiles", "Delivery", "Contact"

Aside from that we are open to designs. One idea we did have was to personalize the site and have a person there somehow to represent the company, making the user feel there are real people behind this site. This is just an idea and not a must.

The name of the company and site is "Copper Ridge Marmora"

Thanks
Updates

Hello All,

Thanks for the great designs. There are some good looking designs that show beautiful kitchens but this site is made for the granite installers and not the retail consumers. So in order not to to confuse the buyers I would like to keep this as much about the raw products as possible. The raw products being the granite slabs, thereby making it obvious we don't sell granite counter tops. 

This design will really be the identity of this company so it is important we get the right message across on this index page and that this page is as complete as possible.

Again, thanks for all the work being put into this.

Target Market(s)

The target audience is granite installers or companies that would with granite slabs.

Industry/Entity Type

Business

```html
<!DOCTYPE html>
<html lang="en">
<head>
<meta charset="utf-8">
<title>Copper Ridge Marmora — Black Granite Slabs and Tiles</title>
<link rel="stylesheet" href="https://fonts.googleapis.com/css2?family=Play:wght@400;700&family=Arimo:wght@400&display=swap">
<style>
  :root {
    --page: #efefef;
    --header-top: #d9d9d9;
    --header-bottom: #fbfbfb;
    --ink: #111111;
    --muted: #666666;
    --line: #1a1a1a;
    --frame: #6e6e6e;
    --green: #3a6a2c;
    --green-dark: #2f4f2a;
    --field-border: #c9c9c9;
    --footer: #1e1e1e;
    --footer-text: #e6e6e6;
    --button-grey: #6b6b6b;
  }
  * { box-sizing: border-box; margin: 0; padding: 0; }
  html, body { width: 1128px; height: 1200px; overflow: hidden; }
  body { background: var(--page); color: var(--ink); font-family: "Arimo", Arial, sans-serif; position: relative; }

  .site-header { position: absolute; left: 0; top: 0; width: 1128px; height: 144px;
    background: linear-gradient(var(--header-top), var(--header-bottom)); border-bottom: 1px solid var(--line); }
  .brand { position: absolute; left: 453px; top: 62px; width: 200px; display: flex; align-items: center; gap: 8px;
    font-family: "Play", sans-serif; font-weight: 700; font-size: 19px; line-height: 1.05; color: var(--ink); }
  .brand-mark { width: 14px; height: 14px; background: var(--green-dark); flex: none; }
  .call-us { position: absolute; left: 897px; top: 16px; font-family: "Arimo", Arial, sans-serif; color: var(--ink); }
  .call-us .label { font-size: 20px; }
  .call-us .number { font-size: 28px; line-height: 1; }
  .main-nav a { position: absolute; top: 104px; font-family: "Play", sans-serif; font-size: 17px; letter-spacing: .5px;
    color: var(--ink); text-decoration: none; }
  .nav-diamond { position: absolute; top: 139px; width: 10px; height: 10px; background: var(--ink); transform: rotate(45deg); }

  .hero { position: absolute; left: 46px; top: 174px; width: 1036px; height: 388px; border: 3px solid var(--frame);
    background: linear-gradient(180deg, #ece5d8 0%, #d8cfc0 45%, #2a2a2c 62%, #0c0c0e 100%); }
  .hero-dots { position: absolute; left: 467px; top: 550px; width: 124px; height: 25px; border-radius: 13px;
    background: var(--green-dark); display: flex; justify-content: center; align-items: center; gap: 7px; }
  .hero-dots span { width: 10px; height: 10px; border-radius: 50%; background: #fff; }
  .hero-dots span.inactive { background: #9aa897; }

  .tagline { position: absolute; left: 54px; top: 604px; font-family: "Play", sans-serif; font-size: 31px; color: var(--ink); white-space: nowrap; }
  .tagline .lead { color: var(--muted); font-size: 27px; }
  .more-button { position: absolute; left: 941px; top: 602px; width: 105px; height: 33px; background: var(--green);
    color: #fff; font-family: "Play", sans-serif; font-size: 20px; display: flex; align-items: center; justify-content: center; gap: 10px; }
  .section-divider { position: absolute; left: 0; top: 666px; width: 1128px; height: 1px; background: var(--line);
    box-shadow: 0 -10px 14px rgba(0,0,0,.07); }

  .product-card { position: absolute; top: 707px; width: 337px; height: 339px; background: #fff;
    border: 3px solid var(--frame); box-shadow: 2px 3px 5px rgba(0,0,0,.25); }
  .product-photo { height: 170px; }
  .product-photo.slab { background: linear-gradient(160deg, #1c1c1c 0%, #2a2a2a 45%, #9a9a9a 75%, #d6d6d6 100%); }
  .product-photo.tiles { background: linear-gradient(180deg, #101010 0%, #1b1b1b 80%, #b5b5b5 100%); }
  .product-card h2 { font-family: "Play", sans-serif; font-weight: 400; font-size: 25px; margin: 22px 0 6px 20px; }
  .product-card p { font-size: 13.5px; line-height: 1.3; margin: 0 30px 0 20px; text-align: justify; }
  .card-more { position: absolute; right: 20px; bottom: 12px; font-family: "Play", sans-serif; font-size: 17px;
    color: var(--green-dark); display: flex; align-items: center; gap: 6px; }

  .contact-panel { position: absolute; left: 782px; top: 708px; width: 303px; }
  .contact-panel h2 { font-family: "Play", sans-serif; font-weight: 400; font-size: 28px; padding-bottom: 6px;
    border-bottom: 3px solid var(--ink); width: 300px; }
  .field { display: block; margin: 17px 0 0 9px; width: 294px; height: 30px; background: #fff; border: 1px solid var(--field-border);
    font-size: 13px; color: #aaa; padding: 7px 8px; }
  .field.message { height: 62px; margin-top: 13px; }
  .field.email { margin-top: 13px; }
  .send { position: absolute; left: 220px; top: 227px; width: 79px; height: 35px; border: 3px solid #fff; outline: 1px solid #ccc;
    background: var(--button-grey); color: #fff; font-size: 17px; display: flex; align-items: center; justify-content: center; }
  .contact-rule { position: absolute; left: 9px; top: 278px; width: 296px; height: 1px; background: var(--ink); }
  .contact-phone { position: absolute; left: 16px; top: 298px; display: flex; align-items: center; gap: 26px; font-size: 32px; }

  .site-footer { position: absolute; left: 0; top: 1080px; width: 1128px; height: 120px; background: var(--footer); }
  .social { position: absolute; top: 16px; width: 35px; height: 33px; background: #d9d9d9; border: 2px solid #888; }
  .copyright { position: absolute; left: 46px; top: 86px; font-size: 12px; color: var(--footer-text); }
  .footer-brand { position: absolute; left: 908px; top: 14px; width: 174px; height: 90px; border: 1px solid #2e2e2e;
    display: flex; align-items: center; justify-content: center; gap: 7px; font-family: "Play", sans-serif; font-weight: 700;
    font-size: 14px; color: #fff; line-height: 1.1; }
  .footer-brand .brand-mark { width: 10px; height: 10px; background: #fff; }
</style>
</head>
<body>
  <header class="site-header">
    <nav class="main-nav">
      <a href="#" style="left:54px">GRANITE SLABS</a>
      <a href="#" style="left:268px">GRANITE TILES</a>
      <a href="#" style="left:721px">DELIVERY</a>
      <a href="#" style="left:900px">CONTACT</a>
    </nav>
    <div class="brand"><span class="brand-mark"></span><span>COPPER RIDGE MARMORA</span></div>
    <div class="call-us"><div class="label">Call us</div><div class="number">555 214 0387</div></div>
    <span class="nav-diamond" style="left:98px"></span>
    <span class="nav-diamond" style="left:305px"></span>
    <span class="nav-diamond" style="left:752px"></span>
    <span class="nav-diamond" style="left:935px"></span>
  </header>

  <div class="hero" role="img" aria-label="Bright dining room with a polished black granite tile floor"></div>
  <div class="hero-dots"><span></span><span></span><span></span><span class="inactive"></span></div>

  <h1 class="tagline"><span class="lead">We are suppliers of</span> Black Granite Slab and Black Granite Tiles</h1>
  <a class="more-button">More
    <svg width="8" height="12" viewBox="0 0 8 12"><path d="M0 0L8 6L0 12Z" fill="#fff"/></svg>
  </a>
  <div class="section-divider"></div>

  <article class="product-card" style="left:37px">
    <div class="product-photo slab" role="img" aria-label="Stack of polished black granite slabs"></div>
    <h2>GRANITE SLAB</h2>
    <p>Lorem ipsum dolor sit amet cons ectetuer adipiscing elit praesent vestibulu moles lacus aenean nonummy.</p>
    <span class="card-more">MORE <svg width="16" height="10" viewBox="0 0 16 10"><path d="M0 5H14M10 1L14 5L10 9" stroke="#2f4f2a" stroke-width="2" fill="none"/></svg></span>
  </article>
  <article class="product-card" style="left:409px">
    <div class="product-photo tiles" role="img" aria-label="Grid of black sparkling granite tiles"></div>
    <h2 style="margin-top:16px">GRANITE TILES</h2>
    <p>Lorem ipsum dolor sit amet cons ectetuer adipiscing elit praesent vestibulu moles lacus aenean nonummy.</p>
    <span class="card-more">MORE <svg width="16" height="10" viewBox="0 0 16 10"><path d="M0 5H14M10 1L14 5L10 9" stroke="#2f4f2a" stroke-width="2" fill="none"/></svg></span>
  </article>

  <section class="contact-panel">
    <h2>Get in touch</h2>
    <div class="field">Name</div>
    <div class="field email">Email</div>
    <div class="field message">Message</div>
    <div class="send">Send</div>
    <div class="contact-rule"></div>
    <div class="contact-phone">
      <svg width="34" height="30" viewBox="0 0 34 30">
        <path d="M2 9C2 3 32 3 32 9L32 12L25 12L24 8C20 7 14 7 10 8L9 12L2 12Z" fill="#111"/>
        <path d="M8 14H26L30 28H4Z" fill="#111"/>
        <circle cx="17" cy="20" r="4" fill="#efefef"/>
      </svg>
      <span>555 214 0387</span>
    </div>
  </section>

  <footer class="site-footer">
    <span class="social" style="left:46px"></span>
    <span class="social" style="left:91px"></span>
    <p class="copyright">Copyright 2013 Copper Ridge Marmora. All right reserved.</p>
    <div class="footer-brand"><span class="brand-mark"></span><span>COPPER RIDGE<br>MARMORA</span></div>
  </footer>
</body>
</html>
```